Business card design for Tarvelo Engineering Tandem

We need a new business card design along with all the necessary to place an order. The company is Tarvelo Engineering Tandem and we recently updated our logo.

```html
<!DOCTYPE html>
<html lang="en">
<head>
<meta charset="UTF-8">
<title>Tarvelo Engineering Tandem — Business Card</title>
<link rel="stylesheet" href="https://fonts.googleapis.com/css2?family=Poppins:wght@400;600;700&display=swap">
<style>
  :root {
    --bg: #c9c9c9;
    --yellow: #e2bf22;
    --ink: #111111;
    --grey: #8c8c8c;
    --grey-dark: #6f6f6f;
    --paper: #ffffff;
  }
  * { box-sizing: border-box; margin: 0; padding: 0; }
  html, body { width: 1200px; height: 900px; overflow: hidden; }
  body {
    background: var(--bg);
    font-family: "Poppins", sans-serif;
    position: relative;
  }
  .card {
    position: absolute;
    width: 525px;
    height: 300px;
    border-radius: 22px;
    overflow: hidden;
    box-shadow: 0 6px 18px rgba(0,0,0,0.18);
  }
  .card--front { left: 90px; top: 110px; background: var(--yellow); }
  .card--back { left: 585px; top: 490px; background: var(--paper); }

  .wordmark {
    display: flex;
    align-items: center;
    gap: 12px;
    font-weight: 700;
    letter-spacing: 0.03em;
    text-transform: uppercase;
    line-height: 1;
    white-space: nowrap;
  }
  .wordmark__square { width: 20px; height: 20px; flex: none; }

  .card--front .wordmark {
    position: absolute;
    left: 0; right: 0; top: 136px;
    justify-content: center;
    font-size: 25px;
    color: var(--ink);
  }
  .card--front .wordmark__square { background: var(--ink); }

  .card--back .wordmark {
    position: absolute;
    left: 48px; top: 46px;
    font-size: 21px;
    color: var(--grey);
  }
  .card--back .wordmark__square { background: var(--yellow); width: 18px; height: 18px; }

  .accent-bar {
    position: absolute;
    left: 0; top: 166px;
    width: 12px; height: 40px;
    background: var(--yellow);
  }
  .person { position: absolute; left: 48px; top: 162px; }
  .person__name {
    font-weight: 600;
    font-size: 21px;
    letter-spacing: 0.03em;
    color: var(--grey-dark);
    line-height: 1.1;
  }
  .person__role {
    font-size: 14px;
    color: var(--yellow);
    line-height: 1.3;
  }
  .contacts {
    position: absolute;
    left: 48px; top: 224px;
    list-style: none;
    font-size: 12.5px;
    color: var(--grey-dark);
  }
  .contacts li { display: flex; align-items: center; gap: 9px; height: 20px; }
  .contacts svg { width: 13px; height: 13px; flex: none; }
  .contacts .highlight { color: var(--yellow); }

  .address {
    position: absolute;
    right: 36px; top: 150px;
    text-align: right;
    font-size: 12.5px;
    line-height: 1.4;
    color: var(--grey);
    font-style: normal;
  }
</style>
</head>
<body>

  <section class="card card--front" aria-label="Business card front">
    <div class="wordmark">
      <span class="wordmark__square"></span>
      <span class="wordmark__name">Tarvelo Engineering Tandem</span>
    </div>
  </section>

  <section class="card card--back" aria-label="Business card back">
    <div class="wordmark">
      <span class="wordmark__square"></span>
      <span class="wordmark__name">Tarvelo Engineering Tandem</span>
    </div>

    <span class="accent-bar"></span>
    <div class="person">
      <p class="person__name">DANIEL REYES</p>
      <p class="person__role">Managing Director</p>
    </div>

    <ul class="contacts">
      <li>
        <svg viewBox="0 0 24 24" fill="var(--yellow)" aria-hidden="true"><path d="M6.6 10.8a15.2 15.2 0 0 0 6.6 6.6l2.2-2.2a1 1 0 0 1 1-.25 11.4 11.4 0 0 0 3.6.57 1 1 0 0 1 1 1V20a1 1 0 0 1-1 1A17 17 0 0 1 3 4a1 1 0 0 1 1-1h3.5a1 1 0 0 1 1 1c0 1.25.2 2.45.57 3.57a1 1 0 0 1-.25 1z"/></svg>
        <span>044-555 210 387</span>
      </li>
      <li>
        <svg viewBox="0 0 24 24" fill="var(--yellow)" aria-hidden="true"><path d="M2 5h20v14H2z M4 7v.4l8 5.2 8-5.2V7z" fill-rule="evenodd"/></svg>
        <span>info@tarvelotandem.com</span>
      </li>
      <li>
        <svg viewBox="0 0 24 24" fill="none" stroke="var(--yellow)" stroke-width="2" aria-hidden="true"><circle cx="12" cy="12" r="9.5"/><path d="M2.5 12h19M12 2.5c3 3 3 16 0 19M12 2.5c-3 3-3 16 0 19"/></svg>
        <span>www.<span class="highlight">tarvelotandem</span>.com</span>
      </li>
    </ul>

    <address class="address">
      18 Harbor Row, Suite 4<br>
      45012, Eastland
    </address>
  </section>

</body>
</html>
```